Law Firm Profile

I need a Law firm Profile design. Something professional, corporate inspired, unique and sophisticated. Preferred colours are blue, grey and white. Completion timeline is 5 days. Details of law firm are in the uploaded document

```html
<!DOCTYPE html>
<html lang="en">
<head>
<meta charset="utf-8">
<title>RKM Advocates – Law Firm Profile</title>
<link rel="stylesheet" href="https://fonts.googleapis.com/css2?family=Cinzel:wght@400;500&family=Oswald:wght@300;400&family=Open+Sans:wdth,wght@75..100,400..700&display=swap">
<style>
  :root {
    --backdrop: #a8a9aa;
    --paper: #f3f3f4;
    --paper-white: #fafafa;
    --navy: #3d5074;
    --navy-deep: #2d3d5c;
    --band: #4a5d80;
    --band-light: #6b7fa3;
    --ink: #2a2f3a;
    --rule: #b9bec7;
    --photo-warm-a: #d9d4cf;
    --photo-warm-b: #34476b;
    --photo-grey-a: #e4e4e4;
    --photo-grey-b: #3a3a3a;
    --photo-sky-a: #8fb7cf;
    --photo-sky-b: #2c4f5e;
  }
  * { margin: 0; padding: 0; box-sizing: border-box; }
  html, body { width: 1118px; height: 1200px; overflow: hidden; }
  body {
    background: var(--backdrop);
    position: relative;
    font-family: "Open Sans", Arial, sans-serif;
    font-stretch: 75%;
    color: var(--ink);
  }
  .page { position: absolute; background: var(--paper); overflow: hidden; }
  .abs { position: absolute; }
  .band {
    position: absolute; left: 0; right: 0; bottom: 0;
    background: linear-gradient(90deg, var(--band), var(--navy) 70%, var(--band-light));
  }
  .frame { position: absolute; border: 0.7px solid var(--rule); }
  .photo { position: absolute; }

  /* Back page */
  .back-page { left: 139px; top: 72px; width: 373px; height: 484px; }
  .section-title {
    font-family: "Oswald", sans-serif; font-weight: 400;
    color: var(--navy); letter-spacing: 0.2px;
  }
  .core-title { left: 56px; top: 57px; font-size: 18px; }
  .core-text { left: 56px; top: 85px; width: 262px; font-size: 6.6px; line-height: 10.1px; }
  .core-photo {
    left: 56px; top: 157px; width: 260px; height: 192px;
    background: linear-gradient(100deg, var(--photo-warm-a) 0%, #f2f1ef 45%, #8c98ae 70%, var(--photo-warm-b) 100%);
  }
  .contact { left: 108px; top: 379px; width: 220px; }
  .contact-head { font-size: 5.6px; font-weight: 700; color: var(--navy-deep); margin-bottom: 8px; }
  .contact-row { display: flex; align-items: flex-start; gap: 6px; font-size: 5.2px; line-height: 7.6px; margin-bottom: 5px; }
  .contact-row svg { width: 6px; height: 6px; flex: none; margin-top: 1px; }

  /* Cover */
  .cover-page { left: 566px; top: 72px; width: 375px; height: 484px; }
  .cover-photo {
    left: 0; top: 207px; width: 375px; height: 260px;
    background: linear-gradient(160deg, var(--photo-grey-a) 0%, #bdbdbd 35%, #6b6b6b 65%, var(--photo-grey-b) 100%);
  }
  .cover-frame { left: 34px; top: 34px; width: 306px; height: 414px; z-index: 2; }
  .cover-rule { left: 0; right: 0; top: 426px; height: 0; border-top: 0.7px solid #555; z-index: 2; }
  .brand-mark { left: 181px; top: 58px; width: 14px; height: 14px; border-radius: 50%; background: var(--navy); }
  .brand-name {
    font-family: "Cinzel", serif; font-weight: 500; color: var(--navy);
    text-align: center; line-height: 1;
  }
  .cover-name { left: 0; width: 375px; top: 110px; font-size: 41px; }
  .cover-name span { display: block; margin-bottom: 3px; }
  .tag-box {
    position: absolute; display: flex; align-items: center; justify-content: center; gap: 6px;
    color: var(--navy); font-stretch: 100%; letter-spacing: 0.3px;
  }
  .tag-box svg { width: 9px; height: 5px; }
  .cover-tag {
    left: 114px; top: 197px; width: 147px; height: 22px; z-index: 3;
    background: var(--paper-white); border: 0.7px solid var(--rule); font-size: 10px;
  }

  /* Spread */
  .spread-left { left: 157px; top: 613px; width: 369px; height: 501px; }
  .spread-right { left: 526px; top: 613px; width: 375px; height: 501px; background: var(--paper-white); }
  .tower-photo {
    left: 14px; top: 17px; width: 336px; height: 173px;
    background: linear-gradient(120deg, var(--photo-sky-a) 0%, #4f7585 40%, var(--photo-sky-b) 70%, #7fa9bf 100%);
  }
  .inside-frame { left: 71px; top: 118px; width: 224px; height: 100px; }
  .inside-name { left: 0; width: 364px; top: 126px; font-size: 29px; color: #fff; }
  .inside-name span { display: block; margin-bottom: 3px; }
  .inside-tag { left: 71px; top: 197px; width: 224px; font-size: 8.6px; }
  .practice-col { top: 233px; font-size: 4.9px; line-height: 7.3px; }
  .practice-col h3 { font-size: 5.6px; font-weight: 700; color: var(--navy); margin-top: 3px; }
  .practice-col p { margin: 0; }
  .col-a { left: 14px; width: 165px; }
  .col-b { left: 193px; width: 153px; top: 231px; }

  .personnel-title { left: 0; width: 375px; text-align: center; top: 17px; font-size: 19px; font-stretch: 100%; }
  .role-tag {
    position: absolute; background: var(--navy); color: #fff;
    font-size: 6.8px; font-weight: 600; line-height: 10px; padding: 0 7px; letter-spacing: 0.1px;
  }
  .person-name { font-size: 9.6px; font-weight: 700; color: var(--ink); }
  .portrait { background: linear-gradient(170deg, #8a8570 0%, #5a5648 55%, #1f1f24 100%); }
  .portrait-b { background: linear-gradient(170deg, #d8d5d0 0%, #a8a49d 50%, #3a3a40 100%); }
  .bio { font-size: 6.3px; line-height: 10.1px; width: 204px; }

  .mgmt-box { left: 16px; top: 357px; width: 341px; height: 124px; background: var(--navy); color: #e9edf4; }
  .mgmt-tab {
    left: 0; top: 11px; width: 120px; height: 11px; background: var(--paper-white);
    color: var(--navy); font-size: 6.8px; font-weight: 700; line-height: 11px; padding-left: 10px;
  }
  .mgmt-text { left: 11px; top: 34px; width: 108px; font-size: 5.9px; line-height: 10.2px; }
  .mgmt-list { list-style: none; font-size: 5.8px; line-height: 14.5px; }
  .mgmt-list li span { display: inline-block; width: 11px; }
  .list-a { left: 146px; top: 45px; }
  .list-b { left: 238px; top: 42px; }
  .support-head { left: 238px; top: 29px; font-size: 5.9px; font-weight: 700; }
</style>
</head>
<body>

<!-- Back page: core values and contacts -->
<section class="page back-page">
  <div class="frame" style="left:25px;top:26px;width:207px;height:264px;"></div>
  <h2 class="abs section-title core-title">CORE VALUES</h2>
  <p class="abs core-text">We take pride in the quality of our legal services in which we incorporate our core values which include integrity, passion, credibility, continuous professional development and excellent client care in the management of our clients' instructions. The firm is regulated by the Legal Practitioners Council, and adherence to legal ethics and conduct forms the backbone of our practice and the firm's culture. We also aim to efficiently harness creative, bespoke and expert solutions to meet every client's particular needs.</p>
  <div class="photo core-photo" role="img" aria-label="Photo of a lawyer smiling and shaking hands with a client in a bright office"></div>

  <div class="abs contact">
    <div class="contact-head">BUSINESS ADDRESS AND CONTACT INFORMATION</div>
    <div class="contact-row">
      <svg viewBox="0 0 10 10"><circle cx="5" cy="5" r="5" fill="#2d3d5c"/><path d="M5 2.2a1.8 1.8 0 0 0-1.8 1.8C3.2 5.4 5 7.6 5 7.6S6.8 5.4 6.8 4A1.8 1.8 0 0 0 5 2.2z" fill="#fff"/><circle cx="5" cy="4" r="0.6" fill="#2d3d5c"/></svg>
      <div>Plot No. 17, Chisokone Road, Sunview Park<br>P.O. Box 41872, Ridgeway, Lusaka, Zambia</div>
    </div>
    <div class="contact-row">
      <svg viewBox="0 0 10 10"><circle cx="5" cy="5" r="5" fill="#2d3d5c"/><rect x="3.4" y="2.3" width="3.2" height="5.4" rx="0.6" fill="#fff"/><rect x="3.9" y="3" width="2.2" height="3.4" fill="#2d3d5c"/></svg>
      <div>+260770123401, +260960234502, +260970345603, +260760456704</div>
    </div>
    <div class="contact-row">
      <svg viewBox="0 0 10 10"><circle cx="5" cy="5" r="5" fill="#2d3d5c"/><path d="M3.2 2.6c.4-.3.8-.2 1 .2l.4.9c.1.3 0 .5-.2.7l-.3.3c.3.7.8 1.2 1.5 1.5l.3-.3c.2-.2.4-.3.7-.2l.9.4c.4.2.5.6.2 1l-.4.4c-1.8.6-4.8-2.4-4.2-4.2z" fill="#fff"/></svg>
      <div>+260 211000457</div>
    </div>
    <div class="contact-row">
      <svg viewBox="0 0 10 10"><circle cx="5" cy="5" r="5" fill="#2d3d5c"/><rect x="2.6" y="3.3" width="4.8" height="3.4" fill="#fff"/><path d="M2.6 3.3L5 5.2l2.4-1.9" stroke="#2d3d5c" stroke-width="0.5" fill="none"/></svg>
      <div>rkmadvocates.office@example.com</div>
    </div>
  </div>
  <div class="band" style="height:17px;"></div>
</section>

<!-- Front cover -->
<section class="page cover-page">
  <div class="photo cover-photo" role="img" aria-label="Black and white photo of two lawyers shaking hands over a desk with a gavel and scales of justice"></div>
  <div class="frame cover-frame"></div>
  <div class="abs cover-rule"></div>
  <div class="abs brand-mark"></div>
  <h1 class="abs brand-name cover-name"><span>RKM</span><span>ADVOCATES</span></h1>
  <div class="tag-box cover-tag">
    <svg viewBox="0 0 9 5"><path d="M0 .5h9M3 2.5h6M0 4.5h9" stroke="#3d5074" stroke-width="0.7"/></svg>
    LAW FIRM PROFILE
    <svg viewBox="0 0 9 5"><path d="M0 .5h9M0 2.5h6M0 4.5h9" stroke="#3d5074" stroke-width="0.7"/></svg>
  </div>
  <div class="band" style="height:18px;"></div>
</section>

<!-- Inside spread: left page -->
<section class="page spread-left">
  <div class="photo tower-photo" role="img" aria-label="Photo of a glass office tower with large law firm lettering on its facade against a blue sky"></div>
  <div class="frame inside-frame"></div>
  <h2 class="abs brand-name inside-name"><span>RKM</span><span>ADVOCATES</span></h2>
  <div class="tag-box inside-tag">
    <svg viewBox="0 0 9 5"><path d="M0 .5h9M3 2.5h6M0 4.5h9" stroke="#3d5074" stroke-width="0.7"/></svg>
    LAW FIRM PROFILE
    <svg viewBox="0 0 9 5"><path d="M0 .5h9M0 2.5h6M0 4.5h9" stroke="#3d5074" stroke-width="0.7"/></svg>
  </div>

  <div class="abs practice-col col-a">
    <p>RKM Advocates is an established legal firm situated in Lusaka, Zambia. The firm was founded in 2013 by Mr Joseph K. Lungu S.C, the current Director of Public Prosecutions. The firm represents a wide range of clients both local and international and is dedicated to providing the highest quality of services in various areas of the law including</p>
    <h3>CORPORATE LAW</h3>
    <p>We provide comprehensive legal services for corporate clients including in the areas of corporate governance, regulatory compliance, due diligence and risk management advisory. We seamlessly manage the legal aspects of our clients' transactions and ensure that all documentary and contractual requirements are professionally and strategically executed;</p>
    <h3>COMMERCIAL LAW</h3>
    <p>We have vast knowledge and experience in navigating complex commercial legal matters, including contract drafting, negotiations and compliance. We are aligned with the international environment and our lawyers keep up to date on evolving rules of international law and any applicable conflict of laws issues. Our lawyers understand the interplay between the evolving digitalisation of the business environment, jurisdictional variances and the legal implications of innovations to the legal environment;</p>
    <h3>ESTATE AND FAMILY LAW</h3>
    <p>We are well versed in handling estate planning, Wills, Trusts, guardianship, divorce and probate matters to address clients' specific legal needs. Our flexible approach in implementing the full range of established dispute resolution methods at appropriate stages of the transactions and matters speaks to the successful management of even the most complex cases;</p>
    <h3>DEBT COLLECTION</h3>
    <p>We efficiently handle the recovery process which is crucial for the businesses, financial institutions and individuals we represent, ensuring that disruptions and cost to our clients are mitigated;</p>
  </div>

  <div class="abs practice-col col-b">
    <h3>CIVIL AND CRIMINAL LITIGATION</h3>
    <p>We have a notable and well respected track record in the area of litigation and all ancillary processes, we have handled major cases in commercial, criminal, constitutional and other areas of the law. We are committed to ensuring that our work is backed by meticulous legal analysis, structure and sound strategy, ensuring that we draw from the benefits of the integrated and multi-faceted nature of our practice to ensure best results for our clients;</p>
    <h3>ADMINISTRATIVE LAW</h3>
    <p>We represent a significant number of clients in the area of public law and have handled a large number of judicial review matters regarding immigration and deportation matters, regulatory infringements among others. We are committed to offering comprehensive guidance, clear communication and swift and appropriate response and high quality strategy from the administrative stage, at first instance, and across all stages of the appeal process. And;</p>
    <h3>LAND LAW</h3>
    <p>We have handled a wide range of land matters including trespass litigation, encroachment, rectifications and conveyancing and manage a substantial caseload of cases.</p>
    <h3>CONSTITUTIONAL LAW</h3>
    <p>We are a leading firm in constitutional law matters and have handled a plethora of presidential, parliamentary and local government election petitions. Our vast expertise in constitutional law is also displayed by our extensive portfolio in handling all manner of novel challenging matters in this area from constitutional interpretation to general constitutional petitions as well as motions. We have a strong database of case-law records and material which enhances our nuanced and detailed understanding of constitutional law enabling us to render well researched legal opinions to our clients.</p>
  </div>
</section>

<!-- Inside spread: right page -->
<section class="page spread-right">
  <h2 class="abs section-title personnel-title">KEY PERSONNEL</h2>

  <div class="role-tag" style="left:16px;top:53px;">MANAGING PARTNER</div>
  <div class="abs person-name" style="left:17px;top:65px;">Naomi Chisala</div>
  <div class="frame" style="left:22px;top:83px;width:107px;height:115px;"></div>
  <div class="photo portrait" style="left:16px;top:91px;width:121px;height:100px;" role="img" aria-label="Portrait photo of the managing partner"></div>
  <p class="abs bio" style="left:155px;top:69px;">Naomi Chisala has more than seven years of experience in various areas of the law including commercial law, mining law, construction law, labour law, company law, constitutional law, human rights law, ICT law, administrative law, legislative drafting, civil and criminal litigation and energy law. She studied law at the Lusaka Metropolitan University, graduated in 2015 and was admitted to the bar in 2016. Since April 2022 she has sat on the licensing committee of the National Energy Licensing Board and is well versed in the matters relating to the energy sector. She is a member of the Press Freedom Defence Network and advocates for digital rights and freedom of expression. She provides legal advisory services to various civil society organizations and undertakes strategic litigation and she holds a postgraduate diploma in legislative drafting and advocates for legislative reform and advancement in various areas of the law.</p>

  <div class="frame" style="left:22px;top:224px;width:107px;height:116px;"></div>
  <div class="photo portrait-b" style="left:16px;top:232px;width:121px;height:99px;" role="img" aria-label="Portrait photo of the associate"></div>
  <div class="role-tag" style="left:155px;top:232px;">ASSOCIATE</div>
  <div class="abs person-name" style="left:155px;top:245px;">Grace Tembo</div>
  <p class="abs bio" style="left:155px;top:267px;">Grace Tembo has over three years of experience in civil litigation, conveyancing, handling corporate and commercial transactions, contract drafting, family law, human rights law, labour disputes, debt recovery as well as administrative law. She studied at Central Open University and graduated in 2016 and was admitted to the Bar in 2020. She is a member of the Public Interest Committee of the Legal Practitioners Council and has a keen interest in human rights matters.</p>

  <div class="abs mgmt-box">
    <div class="abs mgmt-tab">MANAGEMENT STRUCTURE</div>
    <p class="abs mgmt-text">We have a dedicated team of personnel whose primary goal is to provide the highest quality of service in compliance with all applicable rules of professional conduct. Our support team is friendly, skilled and diverse and work together to ensure that the lawyer-client relationship is seamlessly and properly managed.</p>
    <ol class="abs mgmt-list list-a">
      <li><span>1.</span>MANAGING PARTNER</li>
      <li><span>2.</span>PARTNER (S)</li>
      <li><span>3.</span>ASSOCIATE (S)</li>
    </ol>
    <div class="abs support-head">SUPPORT STAFF:</div>
    <ol class="abs mgmt-list list-b">
      <li><span>4.</span>OFFICE MANAGER</li>
      <li><span>5.</span>ASSISTANT OFFICE MANAGER</li>
      <li><span>6.</span>LEGAL CLERK</li>
      <li><span>7.</span>RECEPTIONIST</li>
    </ol>
  </div>
</section>

</body>
</html>
```